LEARN Business Skills so you can Earn a good living

size of the poster is 8”x 10.75" plus 0.25" bleed.
Please leave 1 inch on the bottoum for footer
I want a design a poster that will attract people's attention.
I appreciate a creative ad however the ad should not take away from being able to clearly read the text.
-I also appreciate a simple creative ad that is not too busy.
-you can use graphics, vectors, or pictures of real people.
-however, if you use real people it should be a white male that is wearing a white shirt and look like a professional person.

Target Market(s)

Potential young business people

Industry/Entity Type

education

Requirements
Must have
• easy to read the text
Nice to have
• I would like a "creative" simple ad that is easy to be read
Should not have
• pictures of women

```html
<!DOCTYPE html>
<html lang="en">
<head>
<meta charset="utf-8">
<title>Learn to Earn – Business Enrichment Course</title>
<link href="https://fonts.googleapis.com/css2?family=Bebas+Neue&family=Poppins:wght@300;400;600;700;800&display=swap" rel="stylesheet">
<style>
  :root {
    --ink: #1f1f1f;
    --paper: #ffffff;
    --band: #232323;
    --rule: #c9c9c9;
    --icon: #6a6a6a;
    --soft: #e4e4e4;
    --desk: #7a5a3a;
  }
  * { margin: 0; padding: 0; box-sizing: border-box; }
  html, body { width: 800px; height: 1200px; overflow: hidden; background: var(--paper); }
  .poster { position: relative; width: 800px; height: 1200px; overflow: hidden; font-family: "Poppins", sans-serif; color: var(--ink); background: var(--paper); }

  .hero-photo {
    position: absolute; left: 0; top: 0; width: 800px; height: 892px;
    background:
      linear-gradient(90deg, rgba(255,255,255,0.85) 0%, rgba(255,255,255,0.2) 55%, rgba(255,255,255,0) 100%),
      linear-gradient(180deg, #ffffff 0%, #f4f4f4 25%, #dcdcdc 55%, #cfcfcf 80%, var(--desk) 86%, #6b4d31 100%);
  }

  .headline-learn { position: absolute; left: 40px; top: 48px; width: 560px; height: 240px; }
  .headline-learn text { font-family: "Bebas Neue", sans-serif; font-size: 318px; fill: var(--ink); }

  .headline-earn { position: absolute; left: 44px; top: 292px; font-size: 120px; line-height: 1; letter-spacing: -2px; white-space: nowrap; }
  .headline-earn .to { font-weight: 300; margin-right: 28px; }
  .headline-earn .earn { font-weight: 800; }

  .title-rule { position: absolute; left: 45px; top: 419px; width: 495px; height: 1px; background: var(--rule); }

  .course-title { position: absolute; left: 45px; top: 436px; font-weight: 700; font-size: 37px; line-height: 40px; text-transform: uppercase; }
  .course-tagline { position: absolute; left: 46px; top: 526px; font-weight: 600; font-size: 23px; line-height: 30px; }

  .skills-band { position: absolute; left: 0; top: 892px; width: 800px; height: 308px; background: var(--band); }
  .skills-frame { position: absolute; left: 54px; top: 893px; width: 691px; height: 177px; border: 1px solid var(--rule); border-radius: 18px; }
  .skills-pill {
    position: absolute; left: 96px; top: 866px; width: 606px; height: 50px;
    background: var(--paper); border-radius: 25px;
    font-weight: 700; font-size: 29px; line-height: 50px; text-align: center; text-transform: uppercase; letter-spacing: -0.3px;
  }
  .skill-divider { position: absolute; top: 940px; width: 1px; height: 110px; background: #5a5a5a; }
  .skill { position: absolute; top: 930px; width: 220px; text-align: center; color: var(--paper); }
  .skill svg { display: block; margin: 0 auto 6px; }
  .skill-label { font-weight: 600; font-size: 18px; line-height: 21px; }

  .skill-topics {
    position: absolute; left: 20px; top: 1090px; width: 760px;
    color: var(--paper); font-weight: 300; font-size: 12.6px; line-height: 16px; text-align: center; text-transform: uppercase;
  }
</style>
</head>
<body>
<main class="poster">
  <div class="hero-photo" role="img" aria-label="Photo of a professional man in a white shirt working on a laptop at a wooden desk in a bright office"></div>

  <svg class="headline-learn" viewBox="0 0 560 240" aria-label="Learn">
    <text x="0" y="232" textLength="555" lengthAdjust="spacingAndGlyphs">LEARN</text>
  </svg>

  <h1 class="headline-earn"><span class="to">TO</span><span class="earn">EARN</span></h1>
  <div class="title-rule"></div>

  <h2 class="course-title">Business<br>Enrichment Course</h2>
  <p class="course-tagline">A proven success of helping people<br>in their livelihoods</p>

  <section class="skills-band"></section>
  <div class="skills-frame"></div>
  <div class="skills-pill">Business skills that will help you</div>

  <div class="skill-divider" style="left:282px"></div>
  <div class="skill-divider" style="left:516px"></div>

  <div class="skill" style="left:71px">
    <svg width="62" height="62" viewBox="0 0 62 62">
      <circle cx="31" cy="31" r="30" fill="var(--icon)" stroke="#9a9a9a"/>
      <g fill="none" stroke="#fff" stroke-width="1.6">
        <rect x="20" y="16" width="22" height="18" rx="3"/>
        <circle cx="31" cy="25" r="5"/>
        <path d="M25 34 l-3 12 5-3 3 4 1-13 M37 34 l3 12 -5-3 -3 4"/>
      </g>
    </svg>
    <div class="skill-label">Get a<br>quality job</div>
  </div>

  <div class="skill" style="left:289px; top:933px">
    <svg width="62" height="62" viewBox="0 0 62 62">
      <circle cx="31" cy="31" r="30" fill="var(--icon)" stroke="#9a9a9a"/>
      <g fill="none" stroke="#fff" stroke-width="1.6">
        <rect x="17" y="36" width="5" height="8"/>
        <rect x="25" y="32" width="5" height="12"/>
        <rect x="33" y="28" width="5" height="16"/>
        <rect x="41" y="24" width="5" height="20"/>
        <path d="M16 30 L28 22 L34 25 L46 16 M41 16 h5 v5"/>
      </g>
    </svg>
    <div class="skill-label">Start/grow<br>your business</div>
  </div>

  <div class="skill" style="left:523px; top:931px">
    <svg width="62" height="62" viewBox="0 0 62 62">
      <circle cx="31" cy="31" r="30" fill="var(--icon)" stroke="#9a9a9a"/>
      <g fill="none" stroke="#fff" stroke-width="1.6">
        <rect x="22" y="32" width="24" height="12" rx="1"/>
        <circle cx="34" cy="38" r="3"/>
        <path d="M16 36 h6 M16 40 h6 M16 44 h6 M18 28 L26 22 L31 25 L42 16 M37 16 h5 v5"/>
      </g>
    </svg>
    <div class="skill-label">Increase your<br>salary</div>
  </div>

  <p class="skill-topics">
    Business Admiistration &nbsp;|&nbsp; Small Business Management &nbsp;|&nbsp; Finance | Investments &nbsp;|&nbsp; Computers &nbsp;|&nbsp; Accounting<br>
    Sales &nbsp;|&nbsp; Marketing &nbsp;|&nbsp; Project Management Interviewing Skills &nbsp;|&nbsp; Business Law &nbsp;|&nbsp; Negotiation &nbsp;|&nbsp; Public Speaking<br>
    Import/Export &nbsp;|&nbsp; Information Technoloy &nbsp;|&nbsp; Distribution &nbsp;|&nbsp; Marketing &nbsp;|&nbsp; LedgerPro &nbsp;|&nbsp; Real Estate<br>
    Health Care-Management &nbsp;|&nbsp; MarketHub
  </p>
</main>
</body>
</html>
```